Bright and beautiful business card for a coach

I'm a personal and business coach based in Perth, Australia. I need a business card that whilst subtle and elegant, will stand out and appeal on a table full of cards.

My business name is Fern Mentoring and the business card must represent the warmth and brightness implied in the name, without being gimmicky. It must have a warmth and appeal and be easy to read.

I prefer clean, minimalist designs.

It must align with the feel of my website and socials: https://www.fernmentoring-example.com.au/
https://www.instagram.com/fernmentoringau/
https://www.facebook.com/fernmentoringau
Updates

Hi Designers Thank you so much for taking the time to submit designs. I wonder if I could have explained myself a little better. Most of the designs that have been submitted look rather formal and many have quite corporate looking embellishments on them (to my eye). I would like softer, warmer, more organic. I’m open to people playing about and being more abstract, using softer embellishments (e.g the line drawing flowers and grasses I’ve used in my socials) incorporating other colours from my palette or like the social icons in my email signature (in PDF), perhaps playing with size/oversize, playing with the bleed. Please don’t be constrained by what I’ve already done, it merely needs to compliment. I’m sorry if I’m not using the right words or have led you astray. I’m no designer, but I’ve done my website, socials, email signature etc all myself (my logo was a design contest) and I was really hoping for my business card to be something more creative than I could have made with a template. Reminder: No black cards/sides please. Thank you 😊

Target Market(s)

Individuals, most likely but not all female. Creative thinkers. Likely professionals.

Industry/Entity Type

Business & Personal Coach

Contact Information for Business Card

(Fern Mentoring Logo) Name: Greta Pellham; Title: Business & Personal Coach; Phone number: +61 (0)458 913307; Email: greta@fernmentoring-example.com.au; Website: https://fernmentoring-example.com.au; Social icons for Facebook, Instagram & LinkedIn: @fernmentoringAU. Optional strapline: "A thinking partner to help you cut through the noise"

Font styles to use
Sans Serif

Colors
00AB8E
00BBA5
67D7C9
C6EFE9
E9F9F6
59FF00
82FF00
B8FF75
E3FFCB
F4FFEA
FFC000
F8CF3A
FAE287
FDF2CF
FEFAEE

Requirements
Must have
• Must align with feel of my website and socials. Must have a pop of #FFC000 (possibly whole of one side, or at least a block). Bright or white background. Easy to read.
Nice to have
• Possibly incorporate the sunshine/grass picture I have used in website and socials - will upload.
Should not have
• Must not be black or dark. Not impersonal or corporate looking.

```html
<!DOCTYPE html>
<html lang="en">
<head>
<meta charset="utf-8">
<title>Fern Mentoring – Business Card</title>
<link href="https://fonts.googleapis.com/css2?family=Lato:wght@400;700&family=Dancing+Script:wght@500&display=swap" rel="stylesheet">
<style>
  :root {
    --sun: #FFC000;
    --sun-deep: #F8B400;
    --sun-soft: #F8CF3A;
    --paper: #FFFFFF;
    --ink: #8A8A8A;
    --ink-dark: #6E6E6E;
    --backdrop: #B3B3B3;
  }
  * { margin: 0; padding: 0; box-sizing: border-box; }
  html, body {
    width: 1200px; height: 900px; overflow: hidden;
    background: var(--backdrop);
    font-family: "Lato", sans-serif;
  }
  .canvas {
    position: relative; width: 1200px; height: 900px;
    display: flex; justify-content: center; align-items: center; gap: 90px;
  }
  .card {
    position: relative; width: 330px; height: 540px; overflow: hidden;
    box-shadow: 0 10px 30px rgba(0,0,0,0.18);
  }

  /* Front */
  .card--front { background: var(--sun); }
  .sun-glow {
    position: absolute; left: 15px; top: 120px; width: 300px; height: 300px;
    border-radius: 50%;
    background: radial-gradient(circle, var(--sun-deep) 0 46%, rgba(248,180,0,0.35) 47% 70%, rgba(255,192,0,0) 71%);
  }
  .brand {
    position: absolute; left: 0; right: 0; top: 252px;
    text-align: center; color: var(--paper);
    font-weight: 400; font-size: 25px; letter-spacing: 3px;
  }

  /* Back */
  .card--back { background: var(--paper); }
  .rays {
    position: absolute; left: 0; top: 150px; width: 190px; height: 260px;
    background: radial-gradient(ellipse at 0% 50%, rgba(255,192,0,0.85) 0%, rgba(255,192,0,0.35) 55%, rgba(255,192,0,0) 75%);
  }
  .contact {
    position: absolute; right: 26px; top: 46px; width: 240px; text-align: left;
  }
  .contact__name {
    font-family: "Dancing Script", cursive; font-weight: 500;
    font-size: 34px; color: var(--sun); line-height: 1;
  }
  .contact__title {
    font-size: 12px; color: var(--ink-dark); letter-spacing: 0.3px;
    margin-top: 8px; padding-bottom: 6px;
    border-bottom: 1.5px solid var(--sun);
  }
  .contact__list { list-style: none; margin-top: 8px; }
  .contact__item {
    display: flex; align-items: center; gap: 6px;
    font-size: 11px; color: var(--ink); line-height: 1.6;
  }
  .contact__item svg { width: 9px; height: 9px; flex: none; }
  .social {
    position: absolute; left: 24px; bottom: 30px;
    display: flex; align-items: center; gap: 7px;
    font-size: 13px; color: var(--ink);
  }
  .social__dot { width: 10px; height: 10px; border-radius: 50%; background: var(--sun); }
  .strapline {
    position: absolute; right: 18px; bottom: 22px;
    transform-origin: right bottom; transform: rotate(-90deg) translateX(100%);
    white-space: nowrap; font-size: 12px; color: var(--ink); letter-spacing: 0.2px;
  }
</style>
</head>
<body>
<main class="canvas">
  <section class="card card--front" aria-label="Card front">
    <div class="sun-glow" role="img" aria-label="Large soft sun with faint radiating rays"></div>
    <p class="brand">Fern Mentoring</p>
  </section>

  <section class="card card--back" aria-label="Card back">
    <div class="rays" role="img" aria-label="Yellow sun rays bursting from the left edge"></div>
    <div class="contact">
      <h1 class="contact__name">Greta Pellham</h1>
      <p class="contact__title">Business &amp; Personal Coach</p>
      <ul class="contact__list">
        <li class="contact__item">
          <svg viewBox="0 0 10 10"><path d="M2 1 L4 1 L4.8 3 L3.6 3.8 Q4.6 5.6 6.2 6.4 L7 5.2 L9 6 L9 8 Q9 9 8 9 Q1 8.5 1 2 Q1 1 2 1Z" fill="#FFC000"/></svg>
          +61 (0)458 913307
        </li>
        <li class="contact__item">
          <svg viewBox="0 0 10 10"><rect x="0.5" y="2" width="9" height="6.5" rx="1" fill="#FFC000"/><path d="M1 2.5 L5 5.5 L9 2.5" stroke="#fff" stroke-width="0.9" fill="none"/></svg>
          greta@fernmentoring-example.com.au
        </li>
        <li class="contact__item">
          <svg viewBox="0 0 10 10"><circle cx="5" cy="5" r="4.2" fill="none" stroke="#FFC000" stroke-width="1.2"/><path d="M0.8 5 H9.2 M5 0.8 Q2.5 5 5 9.2 M5 0.8 Q7.5 5 5 9.2" stroke="#FFC000" stroke-width="0.8" fill="none"/></svg>
          www.fernmentoring-example.com.au
        </li>
      </ul>
    </div>
    <p class="social"><span class="social__dot"></span>@fernmentoringAU.</p>
    <p class="strapline">A thinking partner to help you cut through the noise</p>
  </section>
</main>
</body>
</html>
```